Sophisticated, clean website reflecting my feminine, playful side to sell my abstract art,

I need a website no more than 3 pages to showcase my paintings, a little about me and some contact info. I do abstracts so looking for something a little edgy, yet feminine and current.
Updates

Hi there, These are some artists websites that I Iike: Marnelvoss.com (I like how airy it is) peterwallombry.com garethpolvens.com (I like how it scrolls) I'll need a place for a photo ( a headshot-i do not have it yet so I'll need to be able to upload that later) as well as an area for my bio. Also, it's important that I will be able to upload any new photos and descriptions easily so it should be user friendly. Lastly, I like in a sunny place so would like to have this seem upbeat and playful as that is how i like to paint. thanks-I'm trying to upload my photos now -

Target Market(s)

ppl ages 35-70 who want large scale art for their homes

Industry/Entity Type

art

Coding

Coded - Design and coding required

Number of Pages Required

3 page

Colors

Designer to choose colors to be used in the design.

Requirements
Must have
• photos of my art, a place for my bio, be easy to reach me. tasteful-nothing too "in your face" -my clients are pretty high end and organized. They like clean lines
Nice to have
• sophisticated background, muted tones in the back-similar clean font throughout-no cursive
Should not have
• too many dark areas. Too many blocks of color. Too serious.

```html
<!DOCTYPE html>
<html lang="en">
<head>
<meta charset="utf-8">
<title>Clara Wendell — Abstract Art</title>
<link rel="stylesheet" href="https://fonts.googleapis.com/css2?family=Barlow+Condensed:wght@600;700&family=Barlow:wght@500;600;700&family=Didact+Gothic&display=swap">
<style>
  :root {
    --ink: #111111;
    --white: #ffffff;
    --gold: #b98a5a;
    --sage: #c5bd9a;
    --hero-a: #4a6f66;
    --hero-b: #6f7467;
    --frame: #d2a873;
    --portrait: #c9a58c;
    --art-rust: #dcc4b8;
    --art-violet: #c9c0d3;
    --art-rose: #d9c8c2;
    --art-ochre: #d8b865;
    --footer: #000000;
    --rule: #444444;
  }
  * { box-sizing: border-box; margin: 0; padding: 0; }
  html, body { width: 1200px; height: 2985px; overflow: hidden; }
  body {
    position: relative;
    background: var(--white);
    font-family: "Didact Gothic", sans-serif;
    color: var(--ink);
  }
  .abs { position: absolute; }
  .display { font-family: "Barlow Condensed", sans-serif; font-weight: 700; text-transform: uppercase; }

  /* Header */
  .top-band {
    left: 0; top: 0; width: 1200px; height: 114px;
    background: linear-gradient(90deg, #e2e7e3, #efeee9);
  }
  .brand { display: flex; align-items: center; gap: 14px; }
  .brand-square { width: 56px; height: 56px; border: 3px solid var(--ink); }
  .brand-name { font-size: 44px; letter-spacing: 0.5px; color: var(--ink); }
  .header-brand { left: 396px; top: 28px; }
  .follow { right: 132px; top: 42px; display: flex; align-items: center; gap: 14px; }
  .follow-label { font-size: 19px; color: #333; }
  .social-dot { width: 34px; height: 34px; border-radius: 50%; background: var(--ink); }

  /* Nav */
  .main-nav { left: 0; top: 114px; width: 1200px; height: 62px; background: var(--white); }
  .nav-item { top: 18px; font-size: 23px; color: var(--ink); transform: translateX(-50%); }
  .nav-item.is-active::after {
    content: ""; display: block; height: 2px; background: var(--ink); margin-top: 6px;
  }

  /* Hero */
  .hero {
    left: 0; top: 176px; width: 1200px; height: 629px;
    background: linear-gradient(160deg, var(--hero-a), var(--hero-b));
  }
  .hero-title { left: 0; width: 1200px; text-align: center; color: var(--white); line-height: 1; }
  .hero-mark { left: 570px; top: 323px; width: 62px; height: 62px; border: 3px solid var(--white); }
  .hero-line1 { top: 405px; font-size: 62px; }
  .hero-line2 { top: 462px; font-size: 82px; }
  .slide-arrow {
    top: 435px; width: 64px; height: 76px; background: rgba(0,0,0,.35);
    display: flex; align-items: center; justify-content: center;
  }

  /* About */
  .about-wash {
    left: 70px; top: 890px; width: 500px; height: 520px;
    background: linear-gradient(180deg, #fbe6dc, #fdf3ee);
    opacity: .8;
  }
  .portrait-frame {
    left: 182px; top: 932px; width: 305px; height: 395px;
    background: var(--frame);
    padding: 22px;
  }
  .portrait-photo { width: 100%; height: 100%; background: var(--portrait); }
  .section-heading { font-size: 60px; line-height: 1; color: var(--ink); }
  .about-heading { left: 590px; top: 926px; }
  .about-copy { left: 590px; top: 1013px; width: 495px; font-size: 17px; line-height: 27px; text-align: justify; color: #222; }
  .about-copy p + p { margin-top: 15px; }
  .outline-button {
    border: 2px solid var(--ink); background: var(--white);
    font-family: "Barlow", sans-serif; font-weight: 600; color: var(--gold);
    display: flex; align-items: center; justify-content: center; text-transform: uppercase;
  }
  .learn-more { left: 590px; top: 1259px; width: 179px; height: 50px; font-size: 17px; }

  /* Gallery */
  .gallery-wash {
    left: 0; top: 1400px; width: 1200px; height: 700px;
    background: linear-gradient(180deg, #ffffff 0%, #fcece8 40%, #fcece8 75%, #ffffff 100%);
  }
  .section-divider { left: 599px; top: 1400px; width: 2px; height: 78px; background: var(--ink); }
  .gallery-heading { left: 0; width: 1200px; top: 1502px; text-align: center; font-size: 54px; }
  .artwork { top: 1610px; width: 317px; height: 313px; }
  .art-rust { left: 94px; background: var(--art-rust); }
  .art-violet { left: 442px; background: var(--art-violet); }
  .art-rose { left: 789px; background: var(--art-rose); }
  .gallery-arrow { top: 1750px; }
  .view-more { left: 506px; top: 1984px; width: 206px; height: 56px; font-size: 19px; }

  /* Contact */
  .contact-heading { left: 129px; top: 2200px; font-size: 56px; }
  .contact-rule { left: 129px; top: 2266px; width: 75px; height: 2px; background: var(--sage); }
  .contact-copy { left: 129px; top: 2285px; width: 420px; font-size: 18px; line-height: 29px; color: #222; }
  .contact-row { left: 129px; display: flex; align-items: center; gap: 20px; }
  .contact-icon {
    width: 70px; height: 70px; border-radius: 50%; background: var(--sage);
    display: flex; align-items: center; justify-content: center;
  }
  .contact-label { font-size: 17px; color: #333; letter-spacing: .3px; }
  .contact-value-strong { font-family: "Barlow", sans-serif; font-weight: 700; font-size: 23px; }
  .contact-value { font-size: 23px; letter-spacing: .3px; }
  .contact-painting {
    left: 585px; top: 2120px; width: 550px; height: 560px;
    background: var(--art-ochre);
  }

  /* Footer */
  .site-footer { left: 0; top: 2770px; width: 1200px; height: 215px; background: var(--footer); }
  .footer-brand { left: 84px; top: 44px; }
  .footer-brand .brand-square { width: 44px; height: 44px; border-color: var(--white); }
  .footer-brand .brand-name { color: var(--white); font-size: 36px; }
  .footer-link { top: 52px; color: var(--white); font-size: 22px; transform: translateX(-50%); }
  .footer-social { left: 984px; top: 48px; width: 34px; height: 34px; border-radius: 50%; background: var(--white); }
  .footer-rule { left: 68px; top: 128px; width: 992px; height: 1px; background: var(--rule); }
  .copyright { left: 0; width: 1200px; top: 152px; text-align: center; color: #ddd; font-family: "Barlow", sans-serif; font-weight: 500; font-size: 12px; }
</style>
</head>
<body>

  <header>
    <div class="abs top-band" role="img" aria-label="Faded painted texture band"></div>
    <div class="abs brand header-brand">
      <span class="brand-square"></span>
      <span class="display brand-name">Clara Wendell</span>
    </div>
    <div class="abs follow">
      <span class="display follow-label">Follow on:</span>
      <span class="social-dot"></span>
    </div>
  </header>

  <nav class="abs main-nav">
    <a class="abs display nav-item is-active" style="left:229px">Home</a>
    <a class="abs display nav-item" style="left:425px">About Me</a>
    <a class="abs display nav-item" style="left:636px">Gallery</a>
    <a class="abs display nav-item" style="left:845px">Contact</a>
  </nav>

  <section>
    <div class="abs hero" role="img" aria-label="Hero photo of an abstract painting"></div>
    <div class="abs hero-mark"></div>
    <h1 class="abs display hero-title hero-line1">Welcome to</h1>
    <div class="abs display hero-title hero-line2">Clara Wendell</div>
    <div class="abs slide-arrow" style="left:0">
      <svg width="20" height="34" viewBox="0 0 20 34"><path d="M16 3 L4 17 L16 31" fill="none" stroke="#fff" stroke-width="4"/></svg>
    </div>
    <div class="abs slide-arrow" style="left:1146px;width:54px">
      <svg width="20" height="34" viewBox="0 0 20 34"><path d="M4 3 L16 17 L4 31" fill="none" stroke="#fff" stroke-width="4"/></svg>
    </div>
  </section>

  <section>
    <div class="abs about-wash" role="img" aria-label="Soft peach watercolour wash"></div>
    <div class="abs portrait-frame">
      <div class="portrait-photo" role="img" aria-label="Portrait photo of the artist"></div>
    </div>
    <h2 class="abs display section-heading about-heading">About Me</h2>
    <div class="abs about-copy">
      <p>Lorem ipsum dolor sit amet, consectetur adipiscing elit, sed do eiusmod tempor incididunt ut labore et dolore magna aliqua. Ut enim ad minim veniam, quis nostrud exercitation ullamco laboris</p>
      <p>Duis aute irure dolor in reprehenderit in voluptate velit esse cillum dolore eu fugiat nulla pariatur. Excepteur sint occaecat cupidatat non proident, sunt in culpa qui officia deserunt mollit anim id est laborum.Sed ut perspiciatis unde omnis iste natus error</p>
    </div>
    <a class="abs outline-button learn-more">Learn More</a>
  </section>

  <section>
    <div class="abs gallery-wash" role="img" aria-label="Pale pink watercolour background"></div>
    <div class="abs section-divider"></div>
    <h2 class="abs display section-heading gallery-heading">Painting Gallery</h2>
    <svg class="abs gallery-arrow" style="left:44px" width="20" height="34" viewBox="0 0 20 34"><path d="M16 3 L4 17 L16 31" fill="none" stroke="#111" stroke-width="4"/></svg>
    <div class="abs artwork art-rust" role="img" aria-label="Photo of a painting, first in the gallery"></div>
    <div class="abs artwork art-violet" role="img" aria-label="Photo of a painting, second in the gallery"></div>
    <div class="abs artwork art-rose" role="img" aria-label="Photo of a painting, third in the gallery"></div>
    <svg class="abs gallery-arrow" style="left:1126px" width="20" height="34" viewBox="0 0 20 34"><path d="M4 3 L16 17 L4 31" fill="none" stroke="#111" stroke-width="4"/></svg>
    <a class="abs outline-button view-more">View More</a>
  </section>

  <section>
    <h2 class="abs display section-heading contact-heading">Contact</h2>
    <div class="abs contact-rule"></div>
    <p class="abs contact-copy">Lorem ipsum dolor sit amet, consectetur adipiscing elit, sed do eiusmod tempor incididunt ut</p>
    <div class="abs contact-row" style="top:2383px">
      <span class="contact-icon">
        <svg width="36" height="36" viewBox="0 0 24 24"><path d="M6.6 10.8c1.4 2.8 3.8 5.1 6.6 6.6l2.2-2.2c.3-.3.7-.4 1-.2 1.1.4 2.3.6 3.6.6.6 0 1 .4 1 1V20c0 .6-.4 1-1 1C10.6 21 3 13.4 3 4c0-.6.4-1 1-1h3.5c.6 0 1 .4 1 1 0 1.3.2 2.5.6 3.6.1.3 0 .7-.2 1z" fill="#fff"/></svg>
      </span>
      <div>
        <div class="contact-label">PHONE NUMBER</div>
        <div class="contact-value-strong">(123) 456 7890</div>
      </div>
    </div>
    <div class="abs contact-row" style="top:2473px">
      <span class="contact-icon">
        <svg width="40" height="30" viewBox="0 0 40 30"><rect x="2" y="3" width="36" height="24" fill="none" stroke="#fff" stroke-width="2"/><path d="M2 3 L20 17 L38 3 M2 27 L15 14 M38 27 L25 14" fill="none" stroke="#fff" stroke-width="2"/></svg>
      </span>
      <div>
        <div class="contact-label">EMAIL US</div>
        <div class="contact-value">clarawendell@info.com</div>
      </div>
    </div>
    <div class="abs contact-painting" role="img" aria-label="Photo of a painting beside the contact details"></div>
  </section>

  <footer class="abs site-footer">
    <div class="abs brand footer-brand">
      <span class="brand-square"></span>
      <span class="display brand-name">Clara Wendell</span>
    </div>
    <a class="abs display footer-link" style="left:451px">Home</a>
    <a class="abs display footer-link" style="left:574px">About Me</a>
    <a class="abs display footer-link" style="left:711px">Gallery</a>
    <a class="abs display footer-link" style="left:845px">Contact</a>
    <span class="abs footer-social"></span>
    <div class="abs footer-rule"></div>
    <p class="abs copyright">© 2022 CLARA WENDELL | ALL RIGHTS RESERVED</p>
  </footer>

</body>
</html>
```